Private Investigation Business Card Design

I need a business card for a new private investigation company named Brisk Inquiries. I perform mainly surveillance jobs, vehicle repossessions, document serves etc. The final design should aim for a professional look. The logo has a magnifying glass with stick man arms and legs and is in a running action to show the "Brisk" aspect of the name. If the colour scheme could remain the same as the website www.briskinquiries-demo.com.au with silvers,blacks and a couple electric blue highlights.
Industry/Entity Type
Business
Contact Information for Business Card
Morgan Kellaway
Brisk Inquiries
0487316204
PO Box 58, Carnwell NSW 2291
info@briskinquiries-demo.com.au
www.briskinquiries-demo.com.au
Look and feel

```html
<!DOCTYPE html>
<html lang="en">
<head>
<meta charset="utf-8">
<title>Brisk Inquiries – Business Card</title>
<link rel="stylesheet" href="https://fonts.googleapis.com/css2?family=Saira:wght@400;700;800&display=swap">
<style>
  :root {
    --page: #ebe7e1;
    --card: #ffffff;
    --silver: #8c8d92;
    --silver-light: #c9cacf;
    --ink: #1f1f1f;
    --electric-blue: #4a9fd8;
    --footer: #242424;
    --footer-text: #d6d6d6;
  }
  * { box-sizing: border-box; margin: 0; padding: 0; }
  html, body {
    width: 1189px;
    height: 1200px;
    overflow: hidden;
    background: var(--page);
    font-family: "Saira", "Helvetica Neue", Arial, sans-serif;
    color: var(--ink);
  }
  .card {
    position: absolute;
    left: 204px;
    width: 792px;
    height: 488px;
    background: var(--card);
    border-radius: 18px;
    overflow: hidden;
  }
  .card--front { top: 67px; }
  .card--back { top: 627px; }

  .brand {
    position: absolute;
    left: 0;
    right: 0;
    display: flex;
    align-items: center;
    justify-content: center;
    gap: 22px;
  }
  .card--front .brand { top: 200px; }
  .card--back .brand { top: 88px; }
  .brand__name {
    font-weight: 800;
    font-size: 64px;
    line-height: 1;
    color: var(--silver);
    letter-spacing: 1px;
  }
  .brand__mark {
    width: 58px;
    height: 58px;
    border-radius: 50%;
    background: var(--silver-light);
  }

  .name-band {
    position: absolute;
    top: 241px;
    left: 0;
    right: 0;
    height: 45px;
    background: var(--electric-blue);
    color: #fff;
    font-weight: 800;
    font-size: 34px;
    letter-spacing: 1.5px;
    text-transform: uppercase;
    text-align: center;
    line-height: 45px;
  }

  .contact {
    position: absolute;
    top: 312px;
    left: 0;
    right: 0;
    list-style: none;
    text-align: center;
    font-size: 25px;
    line-height: 33px;
    letter-spacing: 0.6px;
  }
  .contact__label { font-weight: 800; margin-right: 6px; }

  .site-bar {
    position: absolute;
    left: 0;
    right: 0;
    bottom: 0;
    height: 59px;
    background: var(--footer);
    color: var(--footer-text);
    text-align: center;
    font-size: 23px;
    letter-spacing: 1px;
    line-height: 59px;
  }
</style>
</head>
<body>
  <section class="card card--front">
    <div class="brand">
      <span class="brand__name">Brisk Inquiries</span>
      <span class="brand__mark"></span>
    </div>
  </section>

  <section class="card card--back">
    <div class="brand">
      <span class="brand__name">Brisk Inquiries</span>
      <span class="brand__mark"></span>
    </div>
    <div class="name-band">Morgan Kellaway</div>
    <ul class="contact">
      <li><span class="contact__label">P:</span>0487316204</li>
      <li><span class="contact__label">E:</span>info@briskinquiries-demo.com.au</li>
      <li><span class="contact__label">A:</span>PO Box 58, Carnwell NSW 2291</li>
    </ul>
    <div class="site-bar">www.briskinquiries-demo.com.au</div>
  </section>
</body>
</html>
```